Wordpress website design for a high-end painting business

We are currently rebranding and are looking to update our Wordpress theme. We have recently rebranded our logo on PixelHarbor, and would like our website to be equally as refined.
Our business is named “Fenwick Painters”. We are a high-end painting business that is known for being professional and having high standards. Our clean and professional image is important as it separates us from our competition. Our current website can be found at www.fenwickcoatings.co.nz . We designed the site ourselves so it is understandably rudimentary. We are generally happy with the. page layout of our existing site, but we like a professional remodel. Any ideas on improvement welcomed.
We would like the front page of the website to summarise all of the info throughout the whole website (I.e introduction, photos, testimonials, contact info etc.) as visitors typically scroll through the first page to see that we are reputable and get to our contact number/email contact at the bottom of the page. We would like this first page to give a clean well rounded image of our business. We would like the gallery to be a scroll through of large photos, as it is difficult to see paint details in smaller photos. A contact page with an enquiry section would also be good.
For the colour scheme, we would like something that fits a bold, masculine and high end theme (similar to our logo attached).
We would like the footer to include Velmora paint logos and the accredited painter logo we have included as these are important to our profession.
We have attached some photos of our work also. I will add more in the coming days. More can also be found on our website.
If you have questions or comments, please don’t hesitate to ask and I will get back as soon as possible.
We are open to your own interpretation or ideas for a better layout/site provided they fit the general brief of being a well rounded site for our profession.
Thanks,
Fenwick Painters.
Target Market(s)
High end clients
Industry/Entity Type
Painting (interior and exterior)
Coding
Coded - Design and coding required
Requirements
Must have
- Classy feel, separating us from typical painting companies. Well rounded homepage.
Nice to have
- Lots of examples of our work
Should not have
- Untidy paint motifs (eg, paint droplets, paint splashes)

```html
<!DOCTYPE html>
<html lang="en">
<head>
<meta charset="utf-8">
<title>Fenwick Painters</title>
<link href="https://fonts.googleapis.com/css2?family=Libre+Baskerville:wght@400;700&family=Arimo:wght@400;700&family=Lato:ital,wght@0,400;1,400&family=Montserrat:wght@500;600&display=swap" rel="stylesheet">
<style>
:root{
  --brown:#8e7558;
  --brown-dark:#6f5a43;
  --gallery:#8c7357;
  --navy:#1e2838;
  --ink:#1d1d1d;
  --muted:#6c6c6c;
  --white:#ffffff;
  --badge:#2a8ad0;
  --badge-edge:#1c5f93;
}
*{box-sizing:border-box;margin:0;padding:0}
html,body{width:1200px;height:3987px;overflow:hidden;background:var(--white)}
body{position:relative;font-family:"Arimo",Arial,sans-serif;color:var(--ink)}
a{color:inherit;text-decoration:none}

/* header */
.site-header{position:absolute;left:0;top:0;width:1200px;height:80px;background:var(--white);z-index:3}
.brand{position:absolute;left:92px;top:0;width:200px;height:150px;background:var(--white);border-radius:0 0 90px 90px;z-index:4;display:flex;align-items:center;justify-content:center;gap:8px}
.brand-dot{width:14px;height:14px;border-radius:50%;background:var(--brown)}
.brand-name{font-family:"Libre Baskerville",Georgia,serif;font-weight:700;font-size:17px;color:var(--ink);line-height:1.2;text-align:center}
.main-nav{position:absolute;left:345px;top:31px;display:flex;gap:30px;font-size:14px}
.main-nav a.active{color:var(--brown)}
.header-cta{position:absolute;left:930px;top:15px;width:158px;height:50px;border-radius:25px;background:var(--navy);color:var(--white);font-weight:700;font-size:15px;display:flex;align-items:center;justify-content:center}

/* hero */
.hero{position:absolute;left:0;top:80px;width:1200px;height:635px;background:linear-gradient(180deg,#6d93c4 0%,#b4a68e 40%,#7c7460 62%,#4e6e34 100%)}
.hero-panel{position:absolute;left:232px;top:185px;width:738px;height:230px;background:rgba(40,40,40,.72);text-align:center;color:var(--white)}
.hero-title{font-family:"Libre Baskerville",Georgia,serif;font-weight:700;font-size:40px;margin-top:40px;letter-spacing:1px}
.hero-text{font-size:14.5px;line-height:30px;margin:8px auto 0;width:640px}
.btn-brown{background:var(--brown);color:var(--white);font-weight:700;font-size:15px;border-radius:25px;display:flex;align-items:center;justify-content:center}
.hero-btn{position:absolute;left:273px;top:170px;width:192px;height:44px}
.round-arrow{position:absolute;width:40px;height:40px;border-radius:50%;background:var(--white);display:flex;align-items:center;justify-content:center;box-shadow:0 2px 6px rgba(0,0,0,.25)}

/* section headings */
.sec-title{position:absolute;left:0;width:1200px;text-align:center;font-family:"Libre Baskerville",Georgia,serif;font-weight:700;font-size:36px;display:flex;justify-content:center;align-items:center;gap:14px}
.heading-mark{display:inline-block;width:30px;height:6px;background:var(--brown)}
.heading-mark.dark{background:var(--navy)}
.heading-mark.long{width:46px;height:8px}

/* about */
.about-title{position:absolute;left:112px;top:810px;font-family:"Libre Baskerville",Georgia,serif;font-weight:700;font-size:36px;display:flex;align-items:center;gap:18px}
.about-text{position:absolute;left:112px;top:875px;width:490px;font-size:12.5px;line-height:28px;color:var(--ink)}
.about-text p+p{margin-top:12px}
.about-btn{position:absolute;left:112px;top:1163px;width:191px;height:50px;box-shadow:0 3px 6px rgba(0,0,0,.25)}
.about-photo{position:absolute;left:624px;top:787px;width:460px;height:460px;border-radius:50%;background:linear-gradient(180deg,#9fb8dc 0%,#d8cfb4 45%,#8e9b6c 75%,#5b7a36 100%);box-shadow:0 6px 18px rgba(0,0,0,.3)}

/* services */
.services{position:absolute;left:0;top:1335px;width:1200px;height:830px;background:linear-gradient(180deg,#2b3648 0%,#263044 60%,#1f2838 100%)}
.services .sec-title{top:70px;color:var(--white)}
.service{position:absolute;width:270px;height:270px;border-radius:50%;display:flex;flex-direction:column;align-items:center;justify-content:center;color:var(--white);font-family:"Libre Baskerville",Georgia,serif;font-weight:700;font-size:16px;text-align:center;line-height:32px;box-shadow:0 6px 16px rgba(0,0,0,.45)}
.service.featured{background:var(--brown);border:5px solid var(--white);font-weight:400}
.service.featured .desc{font-family:"Arimo",Arial,sans-serif;font-size:12px;line-height:23px;width:220px;margin-top:6px}

/* testimonials */
.testimonials .sec-title{top:2240px}
.card{position:absolute;width:298px;height:398px;background:var(--white);box-shadow:0 6px 22px rgba(0,0,0,.14)}
.avatar{position:absolute;left:20px;top:16px;width:84px;height:84px;border-radius:50%;background:linear-gradient(160deg,#c9b7a2,#7d6a59)}
.stars{position:absolute;right:30px;top:45px;color:var(--muted);font-size:13px;letter-spacing:2px}
.card-name{position:absolute;left:30px;top:118px;font-family:"Montserrat",Arial,sans-serif;font-weight:600;font-size:13px;color:var(--ink)}
.card-text{position:absolute;left:30px;top:150px;width:240px;font-family:"Lato",Arial,sans-serif;font-style:italic;font-size:11.5px;line-height:24px;color:var(--muted)}
.t-arrow{position:absolute;top:2794px;width:56px;height:56px;border-radius:50%;background:var(--white);box-shadow:0 4px 12px rgba(0,0,0,.2);display:flex;align-items:center;justify-content:center}

/* gallery */
.gallery{position:absolute;left:0;top:2940px;width:1200px;height:595px;background:var(--gallery)}
.gallery .sec-title{top:90px;color:var(--white)}
.shot{position:absolute;top:165px;width:233px;height:358px;border-radius:40px}

/* footer */
.footer-nav{position:absolute;left:0;top:3644px;width:1200px;display:flex;justify-content:center;gap:34px;font-size:15px}
.contact-label{position:absolute;left:0;top:3698px;width:1200px;text-align:center;color:var(--brown);font-size:16px}
.contact-row{position:absolute;left:0;top:3748px;width:1200px;display:flex;justify-content:center;gap:38px;font-size:15px;color:var(--ink)}
.contact-item{display:flex;align-items:center;gap:14px}
.icon-ring{width:38px;height:38px;border-radius:50%;border:1px solid #bbb;display:flex;align-items:center;justify-content:center}
.partner{position:absolute;top:3821px;height:50px;display:flex;align-items:center;justify-content:center}
.partner-name{left:367px;width:143px;background:var(--navy);color:var(--white);font-family:"Arimo",Arial,sans-serif;font-weight:700;font-size:26px}
.partner-badge{left:522px;width:345px;height:50px;border-radius:4px;background:var(--badge);border:3px solid var(--badge-edge)}
.copyright{position:absolute;left:0;top:3908px;width:1200px;text-align:center;font-size:14px;color:var(--ink)}
</style>
</head>
<body>

<header class="site-header">
  <nav class="main-nav">
    <a class="active">HOME</a><a>SERVICES</a><a>GALLERY</a><a>ABOUT</a><a>CONTACT</a><a>ALL TESTIMONIALS</a>
  </nav>
  <div class="header-cta">Contac Us</div>
</header>
<div class="brand"><span class="brand-dot"></span><span class="brand-name">FENWICK<br>PAINTERS</span></div>

<section class="hero" role="img" aria-label="Photo of a large two-storey house with a manicured garden and flowering roses">
  <div class="hero-panel">
    <h1 class="hero-title">FENWICK PAINTERS</h1>
    <p class="hero-text">Here at Fenwick Painters, we take a lot of pride in our work. We strive to ensure the highest quality paint-work, paying close attention to detail to provide a long lasting finish.</p>
    <div class="btn-brown hero-btn">Get Started</div>
  </div>
  <div class="round-arrow" style="left:70px;top:298px"><svg width="14" height="14" viewBox="0 0 14 14"><path d="M9 2 4 7l5 5" fill="none" stroke="#111" stroke-width="2"/></svg></div>
  <div class="round-arrow" style="left:1090px;top:298px"><svg width="14" height="14" viewBox="0 0 14 14"><path d="M5 2l5 5-5 5" fill="none" stroke="#111" stroke-width="2"/></svg></div>
</section>

<section class="about">
  <h2 class="about-title">About Us <span class="heading-mark long" role="img" aria-label="Heading ornament"></span></h2>
  <div class="about-text">
    <p>Here at Fenwick Painters, we take a lot of pride in our work. We strive to ensure the highest quality paint-work, paying close attention to detail to provide a long lasting finish. Our clients are always our priority, we aim to deliver beyond their expectations.It is our goal to provide an excellent service from start to finish through clear communication, free quoting and transparency with our pricing.</p>
    <p>We take great pride in the preparation of surfaces for painting and only use the best quality products to ensure we achieve the best finish for you. Our qualified interior designer can also assist you with your colour selection as a part of our free colour consultancy service.</p>
  </div>
  <div class="btn-brown about-btn">Read More</div>
  <div class="about-photo" role="img" aria-label="Photo of a freshly painted single-storey home with a grey roof"></div>
</section>

<section class="services">
  <h2 class="sec-title">
    <span class="heading-mark" role="img" aria-label="Heading ornament"></span>
    Our Services
    <span class="heading-mark" role="img" aria-label="Heading ornament"></span>
  </h2>
  <div class="service" style="left:144px;top:179px;background:linear-gradient(180deg,#8ea4c8,#7d6f5c 55%,#567a34)" role="img" aria-label="Photo of an exterior painted house">Exterior Painting</div>
  <div class="service featured" style="left:463px;top:174px">
    <span>Interior Painting</span>
    <span class="desc">Lorem ipsum dolor sit consectetur adipiscing elit, sed do eiusmod tempor incididunt ut labore et dolore</span>
    <svg width="26" height="26" viewBox="0 0 26 26" style="margin-top:16px"><circle cx="13" cy="13" r="11" fill="none" stroke="#fff" stroke-width="1.3"/><path d="M8 11l5 5 5-5" fill="none" stroke="#fff" stroke-width="1.3"/></svg>
  </div>
  <div class="service" style="left:786px;top:179px;background:linear-gradient(120deg,#56604f,#7a8272 50%,#b9c2c9)" role="img" aria-label="Photo of a patterned wallpapered wall">Wallpapering</div>
  <div class="service" style="left:144px;top:475px;background:linear-gradient(135deg,#d9d5d0,#b8b2ab 50%,#e7e4e0)" role="img" aria-label="Photo of a hand plastering a wall">Plastering</div>
  <div class="service" style="left:465px;top:475px;background:linear-gradient(180deg,#8fb0da,#c8c2b4 45%,#7c5a3c 70%,#5d7d37)" role="img" aria-label="Photo of a washed house exterior">Waterblasting &amp; House<br>Cleaning</div>
  <div class="service" style="left:786px;top:475px;background:linear-gradient(180deg,#9db6d6,#6b6a73 45%,#c9c0c7 70%,#a39aa2)" role="img" aria-label="Photo of a painted roof and weatherboard cladding">Roof Painting</div>
</section>

<section class="testimonials">
  <h2 class="sec-title">
    <span class="heading-mark" role="img" aria-label="Heading ornament"></span>
    Testimonials
    <span class="heading-mark" role="img" aria-label="Heading ornament"></span>
  </h2>
  <article class="card" style="left:129px;top:2382px">
    <div class="avatar" role="img" aria-label="Portrait of the reviewer"></div>
    <div class="stars">☆☆☆☆☆</div>
    <div class="card-name">MARTA KOWALCZYK (2019)</div>
    <p class="card-text">Sam and his Team have done an amazing job painting our house. Without a doubt hiring them was our best decision. Attention to detail, great communication, respect towards our needs, working within the budget are just a few things to describe them. I will be recommending Fenwick Painters and Decorators for many years to come. Thank you, guys!</p>
  </article>
  <article class="card" style="left:451px;top:2340px">
    <div class="avatar" role="img" aria-label="Portrait of the reviewer"></div>
    <div class="stars">☆☆☆☆☆</div>
    <div class="card-name">DUNCAN REID (2020)</div>
    <p class="card-text">Very happy with Fenwick decorators. Sam and Ravi did a great job with good communication and attention to detail. Definitely recommend... good value for money!</p>
  </article>
  <article class="card" style="left:772px;top:2382px">
    <div class="avatar" role="img" aria-label="Portrait of the reviewer"></div>
    <div class="stars">☆☆☆☆☆</div>
    <div class="card-name">LAURA FINCH (2020)</div>
    <p class="card-text">We could not be happier with the work done painting the exterior of our two storey home. Sam and Ravi had brilliant communication and the job went very smoothly. Would definitely recommend!</p>
  </article>
  <div class="t-arrow" style="left:537px"><svg width="20" height="10" viewBox="0 0 20 10"><path d="M20 5H2M6 1 2 5l4 4" fill="none" stroke="#111" stroke-width="2"/></svg></div>
  <div class="t-arrow" style="left:606px"><svg width="20" height="10" viewBox="0 0 20 10"><path d="M0 5h18M14 1l4 4-4 4" fill="none" stroke="#111" stroke-width="2"/></svg></div>
</section>

<section class="gallery">
  <h2 class="sec-title">
    <span class="heading-mark dark" role="img" aria-label="Heading ornament"></span>
    Our Gallery
    <span class="heading-mark dark" role="img" aria-label="Heading ornament"></span>
  </h2>
  <div class="shot" style="left:110px;background:linear-gradient(180deg,#a9c0df,#d5ccae 45%,#8a9a66 75%,#4f7532)" role="img" aria-label="Photo of a repainted cottage exterior"></div>
  <div class="shot" style="left:360px;background:linear-gradient(180deg,#3b3b3d,#9a9a9b 40%,#cfcfcf 70%,#8d8d8d)" role="img" aria-label="Photo of a freshly painted empty interior room"></div>
  <div class="shot" style="left:608px;background:linear-gradient(180deg,#2f63c4,#9cb7e2 40%,#7d6f63 60%,#9a9a9a)" role="img" aria-label="Photo of a modern home with painted cladding"></div>
  <div class="shot" style="left:856px;background:linear-gradient(180deg,#7fa6d6,#b7a58a 45%,#6f7a54 75%,#4d6b30)" role="img" aria-label="Photo of a large two-storey house with garden"></div>
  <div class="round-arrow" style="left:52px;top:330px"><svg width="14" height="14" viewBox="0 0 14 14"><path d="M9 2 4 7l5 5" fill="none" stroke="#111" stroke-width="2"/></svg></div>
  <div class="round-arrow" style="left:1107px;top:330px"><svg width="14" height="14" viewBox="0 0 14 14"><path d="M5 2l5 5-5 5" fill="none" stroke="#111" stroke-width="2"/></svg></div>
</section>

<footer class="site-footer">
  <nav class="footer-nav"><a>HOME</a><a>SERVICES</a><a>GALLERY</a><a>ABOUT</a><a>CONTACT</a><a>ALL TESTIMONIALS</a></nav>
  <div class="contact-label">Contact information</div>
  <div class="contact-row">
    <div class="contact-item"><span class="icon-ring"><svg width="16" height="16" viewBox="0 0 24 24"><path d="M6 2l4 4-2 3c1 3 4 6 7 7l3-2 4 4-3 4C10 22 2 14 2 5z" fill="none" stroke="#777" stroke-width="1.6"/></svg></span>Phone: 021 555 0147</div>
    <div class="contact-item"><span class="icon-ring"><svg width="14" height="18" viewBox="0 0 14 18"><path d="M7 17S1 10 1 6.5a6 6 0 0 1 12 0C13 10 7 17 7 17z" fill="none" stroke="#777" stroke-width="1.5"/><circle cx="7" cy="6.5" r="2" fill="#777"/></svg></span>Riverside, Kelmarsh.</div>
    <div class="contact-item"><span class="icon-ring"><svg width="16" height="12" viewBox="0 0 16 12"><rect x="1" y="1" width="14" height="10" fill="none" stroke="#777" stroke-width="1.4"/><path d="M1 1l7 6 7-6" fill="none" stroke="#777" stroke-width="1.4"/></svg></span>Email: hello@fenwickpainters.co.nz</div>
  </div>
  <div class="partner partner-name">Velmora</div>
  <div class="partner partner-badge" role="img" aria-label="Accredited painter certification badge"></div>
  <div class="copyright">© 2022 All Rights Reserved</div>
</footer>

</body>
</html>
```